Vision, Mission and Culture Posters

We have written text paragraphs for our company vision and mission and need them made into a2 or a3 sized posters using our logo for inspiration for colour. Our company culture has 10 paragraphs and we'd like this to be a single poster of a2 or a1. Each poster should have the logo on and share common design. It's not a complex job really.

Industry/Entity Type

It Company

Requirements
Nice to have
• These will be going up on our office wall so need to be clear to read from a distance and look professional but also not stodgy.

```html
<!DOCTYPE html>
<html lang="en">
<head>
<meta charset="utf-8">
<title>Baywise Parking Hire – Vision</title>
<link rel="stylesheet" href="https://fonts.googleapis.com/css2?family=Anton&family=Archivo+Black&display=swap">
<style>
  :root {
    --paper: #ffff8a;
    --panel: #fff200;
    --panel-edge: #b8ad2a;
    --ink: #111111;
    --red: #e1262c;
    --white: #ffffff;
    --yellow: #fff200;
  }
  * { margin: 0; padding: 0; box-sizing: border-box; }
  html, body { width: 849px; height: 1200px; overflow: hidden; background: var(--paper); }
  .poster {
    position: relative;
    width: 849px;
    height: 1200px;
    background: var(--paper);
    border: 2px solid #9a9a9a;
  }
  .poster-panel {
    position: absolute;
    left: 48px; top: 48px; right: 48px; bottom: 48px;
    background: var(--panel);
    border: 3px solid var(--panel-edge);
  }
  .brand-banner {
    position: absolute;
    left: 175px; top: 70px;
    width: 499px; height: 66px;
    background: var(--ink);
    border: 4px solid var(--yellow);
    outline: 3px solid var(--ink);
    border-radius: 14px;
    display: flex; align-items: center; justify-content: center;
    font-family: "Archivo Black", sans-serif;
    font-size: 31px;
    letter-spacing: 0.5px;
    color: var(--yellow);
  }
  .poster-title {
    position: absolute;
    left: 0; right: 0; top: 230px;
    text-align: center;
    font-family: "Anton", sans-serif;
    font-size: 76px;
    line-height: 1;
    color: var(--red);
    letter-spacing: 1px;
  }
  .vision-statement {
    position: absolute;
    left: 0; top: 0;
    width: 849px; height: 1200px;
  }
  .vision-statement text { font-family: "Anton", sans-serif; }
  .brand-sign {
    position: absolute;
    left: 238px; top: 1000px;
    width: 374px; height: 150px;
    background: var(--panel);
    border: 5px solid var(--ink);
    border-radius: 18px;
    display: flex; align-items: center; justify-content: center; gap: 22px;
  }
  .brand-mark {
    width: 44px; height: 44px;
    background: var(--ink);
  }
  .brand-name {
    font-family: "Archivo Black", sans-serif;
    font-size: 30px;
    line-height: 1.15;
    color: var(--ink);
    text-align: center;
  }
</style>
</head>
<body>
  <main class="poster">
    <div class="poster-panel"></div>

    <header class="brand-banner">BAYWISE PARKING HIRE</header>

    <h1 class="poster-title">VISION</h1>

    <svg class="vision-statement" viewBox="0 0 849 1200" aria-label="To provide the most hassle-free parking rental service whilst giving a personal customer experience people want to tell their friends about">
      <path class="statement-badge"
            d="M424 340 C 600 340 745 360 748 630 C 750 880 620 925 424 925 C 230 925 100 885 102 630 C 104 365 250 340 424 340 Z"
            fill="var(--red)" stroke="var(--ink)" stroke-width="7"/>
      <rect class="accent-bar" x="460" y="330" width="270" height="16" fill="var(--yellow)" stroke="var(--ink)" stroke-width="3"/>
      <rect class="accent-bar" x="490" y="498" width="200" height="9" fill="var(--yellow)"/>

      <text x="158" y="560" font-size="70" fill="var(--white)" textLength="300" lengthAdjust="spacingAndGlyphs">TO PROVIDE</text>
      <text x="492" y="560" font-size="62" fill="var(--white)" textLength="198" lengthAdjust="spacingAndGlyphs">THE</text>
      <text x="158" y="612" font-size="48" fill="var(--yellow)" textLength="532" lengthAdjust="spacingAndGlyphs">MOST HASSLE-FREE PARKING</text>
      <text x="158" y="678" font-size="66" fill="var(--ink)" textLength="532" lengthAdjust="spacingAndGlyphs">RENTAL SERVICE</text>
      <text x="158" y="724" font-size="44" fill="var(--white)" textLength="532" lengthAdjust="spacingAndGlyphs">WHILST GIVING A PERSONAL</text>
      <text x="158" y="780" font-size="56" fill="var(--yellow)" textLength="532" lengthAdjust="spacingAndGlyphs">CUSTOMER EXPERIENCE</text>
      <text x="158" y="822" font-size="36" fill="var(--white)" textLength="532" lengthAdjust="spacingAndGlyphs">PEOPLE WANT TO TELL THEIR FRIENDS ABOUT</text>
    </svg>

    <footer class="brand-sign">
      <span class="brand-mark"></span>
      <span class="brand-name">Baywise<br>Parking Hire</span>
    </footer>
  </main>
</body>
</html>
```